Nivel Crest - Powerpoint Templates

We are a consultancy to help builders to optimize their planning in order to save building costs. For that reason we need templates for teasers and presentations where we offer our services, show our team and their capacities and present workflows, organization charts, price lists etc.

```html
<!DOCTYPE html>
<html lang="en">
<head>
<meta charset="utf-8">
<title>Nivel Crest – Presentation Templates</title>
<link href="https://fonts.googleapis.com/css2?family=Montserrat:wght@400;500;600;700&family=Bebas+Neue&display=swap" rel="stylesheet">
<style>
:root{
  --stage:#8f9094;
  --gold:#c48a2a;
  --gold-lt:#f1cd72;
  --gold-dk:#a8751f;
  --ink:#222226;
  --dark:#2b2b30;
  --text:#3a3a3a;
  --grey:#9b9b9e;
  --white:#ffffff;
}
*{margin:0;padding:0;box-sizing:border-box}
html,body{width:1104px;height:1200px;overflow:hidden;background:var(--stage);font-family:"Montserrat",sans-serif}
.canvas{position:relative;width:1104px;height:1200px}
.slide{position:absolute;width:260px;height:163px;background:var(--white);overflow:hidden;box-shadow:0 7px 6px -4px rgba(0,0,0,.4)}
.slide.gold{background:linear-gradient(100deg,var(--gold-dk) 0%,var(--gold-lt) 45%,var(--gold) 100%)}
.slide.dark{background:linear-gradient(110deg,#1d1d22 0%,#3a3a40 40%,#8a8a90 50%,#3a3a40 60%,#26262b 100%)}
.heading{position:absolute;left:10px;top:6px;font-size:7.6px;font-weight:500;color:var(--ink)}
.heading b{font-weight:500;color:var(--gold)}
.gold .heading,.dark .heading,.gold .heading b,.dark .heading b{color:var(--white)}
.p{font-size:2.3px;line-height:1.4;color:var(--text);text-align:justify}
.gold .p,.dark .p{color:#fff}
.foot{position:absolute;left:0;right:0;bottom:8px;height:6px;display:flex;align-items:center}
.foot .tick{width:3px;height:6px;background:var(--gold)}
.foot .mark{width:52px;padding-left:7px;display:flex;align-items:center;gap:1.5px;font-size:3.4px;font-weight:700;color:var(--ink);white-space:nowrap}
.gold .foot .mark,.dark .foot .mark{color:#fff}
.gold .foot .tick,.dark .foot .tick{background:var(--dark)}
.foot .mark i{width:3px;height:3px;background:var(--gold);display:block}
.foot .bar{flex:1;height:4.5px;background:linear-gradient(90deg,var(--gold),var(--gold-lt) 50%,var(--gold));display:flex;justify-content:space-between;align-items:center;padding:0 8px 0 64px;font-size:2.3px;color:#fff}
.gold .foot .bar{background:linear-gradient(90deg,#2a2a2e,#444 50%,#2a2a2e)}
.photo{position:absolute;inset:0}
.abs{position:absolute}
.t5{font-size:4.6px;font-weight:500;color:var(--ink)}
.gold .t5,.dark .t5{color:#fff}
.sub{font-size:5px;font-weight:600;color:var(--gold)}
.circ{width:17px;height:17px;border-radius:50%;background:var(--dark);display:flex;align-items:center;justify-content:center;flex:none}
.circ.g{background:linear-gradient(135deg,var(--gold-lt),var(--gold))}
.circ span{width:6px;height:6px;border:1px solid #fff;border-radius:50%}
.item{position:absolute;display:flex;gap:5px;width:115px}
.item .txt{border-left:.5px solid #bbb;padding-left:4px;width:88px}
.item .txt .t5{margin-bottom:1px}
.hexrow{position:absolute;left:128px;width:124px;display:flex;align-items:center;gap:8px}
.hexrow svg{flex:none}
.hexrow .txt{width:96px}
.hexrow .t5{font-size:4.2px;color:#fff;margin-bottom:1px}
ul.bul{list-style:none}
ul.bul li{position:relative;padding-left:5px;margin-bottom:5px}
ul.bul li:before{content:"";position:absolute;left:0;top:1px;width:1.3px;height:1.3px;background:#333}
.gold ul.bul li:before{background:#fff}
table.grid{border-collapse:collapse;width:240px;font-size:2.6px;color:var(--ink)}
table.grid th{background:var(--grey);color:#fff;font-weight:500;height:11px;text-align:center}
table.grid th:first-child{text-align:left;padding-left:2px}
table.grid td{height:10.8px;border-bottom:.5px solid #bbb;text-align:center}
table.grid td:first-child{text-align:left;padding-left:2px}
.big{font-family:"Bebas Neue",sans-serif;line-height:1;text-align:center}
</style>
</head>
<body>
<main class="canvas">

<!-- Cover -->
<section class="slide" style="left:111px;top:104px">
  <div class="photo" role="img" aria-label="City skyline at dusk under a hazy blue sky" style="background:linear-gradient(180deg,#51657c 0%,#2b3644 45%,#13171c 100%)"></div>
  <div class="abs" style="left:0;right:0;top:33px;display:flex;justify-content:center;align-items:center;gap:3px;font-size:9px;font-weight:700;color:#fff"><i style="width:7px;height:7px;border:1px solid #fff;display:block"></i>NIVEL CREST</div>
  <div class="abs big" style="left:0;right:0;top:103px;font-size:21px;color:#fff">PRESENTATION</div>
  <div class="abs big" style="left:0;right:0;top:124px;font-size:21px;color:var(--gold-lt)">TITLE GOESHERE</div>
  <div class="abs" style="left:0;right:0;top:144px;text-align:center;font-size:5px;color:#fff">Subtitle of Presentation Goes Here</div>
</section>

<!-- Text two columns -->
<section class="slide" style="left:421px;top:104px">
  <div class="heading"><b>Heading</b> Goes Here</div>
  <div class="abs" style="left:17px;top:35px;width:108px">
    <p class="p">Lorem ipsum dolor sit amet, consectetuer adipiscing elit, sed diam nonummy nibh euismod tincidunt ut laoreet dolore magna aliquam erat volutpat. Ut wisi enim ad minim veniam, quis nostrud exerci tation ullamcorper suscipit lobortis nisl ut aliquip ex ea commodo consequat. Duis autem vel eum iriure dolor in hendre</p><br>
    <p class="p">Lorem ipsum dolor sit amet, consectetuer adipiscing elit, sed diam nonummy nibh euismod tincidunt ut laoreet dolore magna aliquam erat volutpat. Ut wisi enim ad minim veniam, quis nostrud exerci tation ullamcorper suscipit lobortis nisl ut aliquip ex ea commodo consequat. Duis autem vel eum iriure dolor in hendre</p><br>
    <p class="p">Lorem ipsum dolor sit amet, consectetuer adipiscing elit, sed diam nonummy nibh euismod tincidunt ut laoreet dolore magna aliquam erat volutpat. Ut wisi enim ad minim veniam, quis nostrud exerci tation ullamcorper suscipit lobortis nisl ut aliquip ex ea commodo consequat. Duis autem vel eum iriure dolor in hendre Lorem ipsum dolor sit amet, consectetuer adipiscing elit, sed diam nonummy nibh euismod tincidunt ut laoreet dolore magna aliquam erat volutpat. Ut wisi enim ad minim veniam, quis nostrud exerci tation ullamcorper suscipit lobortis nisl ut aliquip ex ea commodo consequat. Duis autem vel eum iriure dolor in hendre</p>
  </div>
  <div class="abs" style="left:136px;top:35px;width:108px">
    <p class="p">Lorem ipsum dolor sit amet, consectetuer adipiscing elit, sed diam nonummy nibh euismod tincidunt ut laoreet dolore magna aliquam erat volutpat. Ut wisi enim ad minim veniam, quis nostrud exerci tation ullamcorper suscipit lobortis nisl ut aliquip ex ea commodo consequat. Duis autem vel eum iriure dolor in hendre</p><br>
    <p class="p">Lorem ipsum dolor sit amet, consectetuer adipiscing elit, sed diam nonummy nibh euismod tincidunt ut laoreet dolore magna aliquam erat volutpat. Ut wisi enim ad minim veniam, quis nostrud exerci tation ullamcorper suscipit lobortis nisl ut aliquip ex ea commodo consequat. Duis autem vel eum iriure dolor in hendre</p><br>
    <p class="p">Lorem ipsum dolor sit amet, consectetuer adipiscing elit, sed diam nonummy nibh euismod tincidunt ut laoreet dolore magna aliquam erat volutpat. Ut wisi enim ad minim veniam, quis nostrud exerci tation ullamcorper suscipit lobortis nisl ut aliquip ex ea commodo consequat. Duis autem vel eum iriure dolor in hendre Lorem ipsum dolor sit amet, consectetuer adipiscing elit, sed diam nonummy nibh euismod tincidunt ut laoreet dolore magna aliquam erat volutpat. Ut wisi enim ad minim veniam, quis nostrud exerci tation ullamcorper suscipit lobortis nisl ut aliquip ex ea commodo consequat. Duis autem vel eum iriure dolor in hendre</p>
  </div>
  <div class="foot"><span class="tick"></span><span class="mark"><i></i>NIVEL CREST</span><span class="bar"><span>www.nivelcrest.com</span><span>PAGE 01</span></span></div>
</section>

<!-- Mission / Vision -->
<section class="slide" style="left:732px;top:104px">
  <div class="abs" style="left:12px;top:24px;font-size:11.5px;font-weight:600;line-height:1;color:var(--ink)">OUR MISSION<br><span style="color:var(--gold)">OUR VISION</span></div>
  <div class="abs" style="left:12px;top:56px;width:110px">
    <p class="p">Lorem ipsum dolor sit amet, consectetuer adipiscing elit, sed diam nonummy nibh euismod tincidunt ut laoreet dolore magna aliquam erat volutpat. Ut wisi enim ad minim veniam, quis nostrud exerci tation ullamcorper suscipit lobortis nisl ut aliquip ex ea commodo consequat. Duis autem vel eum iriure dolor in hendre</p><br>
    <p class="p">Lorem ipsum dolor sit amet, consectetuer adipiscing elit, sed diam nonummy nibh euismod tincidunt ut laoreet dolore magna aliquam erat volutpat. Ut wisi enim ad minim veniam, quis nostrud exerci tation ullamcorper suscipit lobortis nisl ut aliquip ex ea commodo consequat. Duis autem vel eum iriure dolor in hendre Lorem ipsum dolor sit amet, consectetuer adipiscing elit, sed diam nonummy nibh euismod tincidunt ut laoreet dolore magna aliquam erat volutpat. Ut wisi enim ad minim veniam, quis nostrud exerci tation ullamcorper suscipit lobortis nisl ut aliquip ex ea commodo.</p>
  </div>
  <div class="abs" style="left:140px;top:32px;width:120px;height:40px;background:linear-gradient(90deg,var(--gold),var(--gold-lt) 60%,var(--gold))"></div>
  <div class="abs" style="left:140px;top:92px;width:120px;height:40px;background:linear-gradient(90deg,#4a4a50,#1f1f24)"></div>
  <svg class="abs" style="left:126px;top:34px" width="30" height="36" viewBox="0 0 30 36"><polygon points="15,1 29,9 29,27 15,35 1,27 1,9" fill="var(--gold)"/><polygon points="15,5 26,11 26,25 15,31 4,25 4,11" fill="var(--dark)"/><circle cx="15" cy="16" r="4" fill="none" stroke="#fff"/><rect x="13.5" y="21" width="3" height="3" fill="#fff"/></svg>
  <svg class="abs" style="left:126px;top:94px" width="30" height="36" viewBox="0 0 30 36"><polygon points="15,1 29,9 29,27 15,35 1,27 1,9" fill="var(--dark)"/><polygon points="15,5 26,11 26,25 15,31 4,25 4,11" fill="var(--gold)"/><path d="M8 19 L13 15 L17 17 L22 14 M10 20 L15 22 L20 18" stroke="#fff" fill="none" stroke-width="1.3"/></svg>
  <div class="abs" style="left:161px;top:36px;width:92px"><div class="t5" style="color:#fff;font-size:4px">Title Goes Here</div><p class="p" style="color:#fff">Lorem ipsum dolor sit amet, consectetuer adipiscing elit, sed diam nonummy nibh euismod tincidunt ut laoreet dolore magna aliquam erat volutpat. Ut wisi enim ad minim veniam, quis nostrud exerci tation ullamcorper suscipit lobortis nisl ut aliquip ex ea commodo consequat. Duis</p></div>
  <div class="abs" style="left:161px;top:96px;width:92px"><div class="t5" style="color:#fff;font-size:4px">Title Goes Here</div><p class="p" style="color:#fff">Lorem ipsum dolor sit amet, consectetuer adipiscing elit, sed diam nonummy nibh euismod tincidunt ut laoreet dolore magna aliquam erat volutpat. Ut wisi enim ad minim veniam, quis nostrud exerci tation ullamcorper suscipit lobortis nisl ut aliquip ex ea commodo consequat. Duis</p></div>
  <div class="foot"><span class="tick"></span><span class="mark"><i></i>NIVEL CREST</span><span class="bar"><span>www.nivelcrest.com</span><span>PAGE 01</span></span></div>
</section>

<!-- Services -->
<section class="slide" style="left:111px;top:315px">
  <div class="heading"><b>Heading</b> Goes Here</div>
  <div class="abs" style="left:10px;top:26px;width:240px">
    <div class="sub" style="margin-bottom:3px">Service Title Goes Here</div>
    <p class="p">Lorem ipsum dolor sit amet, consectetuer adipiscing elit, sed diam nonummy nibh euismod tincidunt ut laoreet dolore magna aliquam erat volutpat. Ut wisi enim ad minim veniam, quis nostrud exerci tation ullamcorper suscipit lobortis nisl ut aliquip ex ea commodo consequat. Duis autem vel eum iriure dolor in hendrerit in vulputate velit esse molestie consequat, vel illum dolore eu feugiat nulla facilisis at vero eros et accumsan et iusto odio dignissim qui blandit praesent luptatum zzril</p><br>
    <p class="p">Lorem ipsum dolor sit amet, consectetuer adipiscing elit, sed diam nonummy nibh euismod tincidunt ut laoreet dolore magna aliquam erat volutpat. Ut wisi enim ad minim veniam, quis nostrud exerci tation ullamcorper suscipit lobortis nisl ut aliquip ex ea commodo consequat. Duis autem vel eum iriure dolor in hendrerit in vulputate velit esse molestie consequat, vel illum dolore eu feugiat nulla facilisis at vero eros et accumsan et iusto odio dignissim qui blandit praesent luptatum zzril. Lorem ipsum dolor sit amet, consectetuer adipiscing elit, sed diam nonummy nibh euismod tincidunt ut laoreet dolore magna aliquam erat volutpat ullamcorper suscipit lobortis nisl ut aliquipet accumsan</p>
    <div class="sub" style="margin:4px 0 3px">Service Title Goes Here</div>
    <p class="p">Lorem ipsum dolor sit amet, consectetuer adipiscing elit, sed diam nonummy nibh euismod tincidunt ut laoreet dolore magna aliquam erat volutpat. Ut wisi enim ad minim veniam, quis nostrud exerci tation ullamcorper suscipit lobortis nisl ut aliquip ex ea commodo consequat. Duis autem vel eum iriure dolor in hendrerit in vulputate velit esse molestie consequat, vel illum dolore eu feugiat nulla facilisis at vero eros et accumsan et iusto odio dignissim qui blandit praesent luptatum zzril dolore magna aliquam erat volutpat. Ut wisi enim ad minim veniam, quis nostrud exerci tation ullamcorper suscipit lobortis nisl ut aliquip ex ea commodo consequat. Duis autem vel eum iriure dolor in hendrerit in vulputate praes</p>
  </div>
  <div class="foot"><span class="tick"></span><span class="mark"><i></i>NIVEL CREST</span><span class="bar"><span>www.nivelcrest.com</span><span>PAGE 01</span></span></div>
</section>

<!-- Icon list on white -->
<section class="slide" style="left:421px;top:315px">
  <div class="heading"><b>Heading</b> Goes Here</div>
  <div class="item" style="left:10px;top:46px"><div class="circ"><span></span></div><div class="txt"><div class="t5">Title Goes Here</div><p class="p">Lorem ipsum dolor sit amet, consectetuer adipiscing elit, sed diam nonummy nibh euismod tincidunt ut laoreet dolore magna aliquam erat volutpat. Ut wisi enim ad minim veniam, quis nostrud exerci tation ullamcorper suscipit lobortis nisl ut</p></div></div>
  <div class="item" style="left:131px;top:46px"><div class="circ"><span></span></div><div class="txt"><div class="t5">Title Goes Here</div><p class="p">Lorem ipsum dolor sit amet, consectetuer adipiscing elit, sed diam nonummy nibh euismod tincidunt ut laoreet dolore magna aliquam erat volutpat. Ut wisi enim ad minim veniam, quis nostrud exerci tation ullamcorper suscipit lobortis nisl ut</p></div></div>
  <div class="item" style="left:10px;top:78px"><div class="circ g"><span></span></div><div class="txt"><div class="t5">Title Goes Here</div><p class="p">Lorem ipsum dolor sit amet, consectetuer adipiscing elit, sed diam nonummy nibh euismod tincidunt ut laoreet dolore magna aliquam erat volutpat. Ut wisi enim ad minim veniam, quis nostrud exerci tation ullamcorper suscipit lobortis nisl ut</p></div></div>
  <div class="item" style="left:131px;top:78px"><div class="circ g"><span></span></div><div class="txt"><div class="t5">Title Goes Here</div><p class="p">Lorem ipsum dolor sit amet, consectetuer adipiscing elit, sed diam nonummy nibh euismod tincidunt ut laoreet dolore magna aliquam erat volutpat. Ut wisi enim ad minim veniam, quis nostrud exerci tation ullamcorper suscipit lobortis nisl ut</p></div></div>
  <div class="item" style="left:10px;top:111px"><div class="circ"><span></span></div><div class="txt"><div class="t5">Title Goes Here</div><p class="p">Lorem ipsum dolor sit amet, consectetuer adipiscing elit, sed diam nonummy nibh euismod tincidunt ut laoreet dolore magna aliquam erat volutpat. Ut wisi enim ad minim veniam, quis nostrud exerci tation ullamcorper suscipit lobortis nisl ut</p></div></div>
  <div class="item" style="left:131px;top:111px"><div class="circ"><span></span></div><div class="txt"><div class="t5">Title Goes Here</div><p class="p">Lorem ipsum dolor sit amet, consectetuer adipiscing elit, sed diam nonummy nibh euismod tincidunt ut laoreet dolore magna aliquam erat volutpat. Ut wisi enim ad minim veniam, quis nostrud exerci tation ullamcorper suscipit lobortis nisl ut</p></div></div>
  <div class="foot"><span class="tick"></span><span class="mark"><i></i>NIVEL CREST</span><span class="bar"><span>www.nivelcrest.com</span><span>PAGE 01</span></span></div>
</section>

<!-- Gold with hex list -->
<section class="slide gold" style="left:732px;top:315px">
  <div class="heading">Heading Goes Here</div>
  <div class="abs" style="left:12px;top:36px;width:95px">
    <p class="p">Lorem ipsum dolor sit amet, consectetuer adipiscing elit, sed diam nonummy nibh euismod tincidunt ut laoreet dolore magna aliquam erat volutpat. Ut wisi enim ad minim veniam, quis nostrud exerci tation ullamcorper suscipit lobortis nisl ut aliquip ex ea commodo consequat. Duis autem vel eum iriure dolor</p><br>
    <p class="p">Lorem ipsum dolor sit amet, consectetuer adipiscing elit, sed diam nonummy nibh euismod tincidunt ut laoreet dolore magna aliquam erat volutpat. Ut wisi enim ad minim veniam, quis nostrud exerci tation ullamcorper suscipit lobortis nisl ut aliquip ex ea commodo consequat. Duis autem vel eum iriure dolor in hendre</p><br>
    <p class="p">Lorem ipsum dolor sit amet, consectetuer adipiscing elit, sed diam nonummy nibh euismod tincidunt ut laoreet dolore magna aliquam erat volutpat. Ut wisi enim ad minim veniam, quis nostrud exerci tation ullamcorper suscipit lobortis nisl ut aliquip ex ea commodo consequat. Duis autem vel eum iriure dolor in hendre</p>
  </div>
  <div class="hexrow" style="top:30px"><svg width="18" height="21" viewBox="0 0 18 21"><polygon points="9,0 17,5 17,16 9,21 1,16 1,5" fill="var(--dark)"/><circle cx="9" cy="10.5" r="3" fill="none" stroke="#fff" stroke-width=".8"/></svg><div class="txt"><div class="t5">Title Goes Here</div><p class="p">Lorem ipsum dolor sit amet, consectetuer adipiscing elit, sed diam nonummy nibh euismod tincidunt ut laoreet dolore magna aliquam erat volutpat. Ut wisi enim ad minim veniam, quis nostrud exerci tation ullamcorper suscipit</p></div></div>
  <div class="hexrow" style="top:56px"><svg width="18" height="21" viewBox="0 0 18 21"><polygon points="9,0 17,5 17,16 9,21 1,16 1,5" fill="var(--dark)"/><circle cx="9" cy="10.5" r="3" fill="none" stroke="#fff" stroke-width=".8"/></svg><div class="txt"><div class="t5">Title Goes Here</div><p class="p">Lorem ipsum dolor sit amet, consectetuer adipiscing elit, sed diam nonummy nibh euismod tincidunt ut laoreet dolore magna aliquam erat volutpat. Ut wisi enim ad minim veniam, quis nostrud exerci tation ullamcorper suscipit</p></div></div>
  <div class="hexrow" style="top:82px"><svg width="18" height="21" viewBox="0 0 18 21"><polygon points="9,0 17,5 17,16 9,21 1,16 1,5" fill="var(--dark)"/><circle cx="9" cy="10.5" r="3" fill="none" stroke="#fff" stroke-width=".8"/></svg><div class="txt"><div class="t5">Title Goes Here</div><p class="p">Lorem ipsum dolor sit amet, consectetuer adipiscing elit, sed diam nonummy nibh euismod tincidunt ut laoreet dolore magna aliquam erat volutpat. Ut wisi enim ad minim veniam, quis nostrud exerci tation ullamcorper suscipit</p></div></div>
  <div class="hexrow" style="top:108px"><svg width="18" height="21" viewBox="0 0 18 21"><polygon points="9,0 17,5 17,16 9,21 1,16 1,5" fill="var(--dark)"/><circle cx="9" cy="10.5" r="3" fill="none" stroke="#fff" stroke-width=".8"/></svg><div class="txt"><div class="t5">Title Goes Here</div><p class="p">Lorem ipsum dolor sit amet, consectetuer adipiscing elit, sed diam nonummy nibh euismod tincidunt ut laoreet dolore magna aliquam erat volutpat. Ut wisi enim ad minim veniam, quis nostrud exerci tation ullamcorper suscipit</p></div></div>
  <div class="foot"><span class="tick"></span><span class="mark"><i></i>NIVEL CREST</span><span class="bar"><span>www.nivelcrest.com</span><span>PAGE 01</span></span></div>
</section>

<!-- Dark icon list -->
<section class="slide dark" style="left:111px;top:516px">
  <div class="heading">Heading Goes Here</div>
  <div class="item" style="left:10px;top:42px"><div class="circ g"><span></span></div><div class="txt"><div class="t5">Title Goes Here</div><p class="p">Lorem ipsum dolor sit amet, consectetuer adipiscing elit, sed diam nonummy nibh euismod tincidunt ut laoreet dolore magna</p></div></div>
  <div class="item" style="left:131px;top:42px"><div class="circ g"><span></span></div><div class="txt"><div class="t5">Title Goes Here</div><p class="p">Lorem ipsum dolor sit amet, consectetuer adipiscing elit, sed diam nonummy nibh euismod tincidunt ut laoreet dolore magna</p></div></div>
  <div class="item" style="left:10px;top:74px"><div class="circ g"><span></span></div><div class="txt"><div class="t5">Title Goes Here</div><p class="p">Lorem ipsum dolor sit amet, consectetuer adipiscing elit, sed diam nonummy nibh euismod tincidunt ut laoreet dolore magna</p></div></div>
  <div class="item" style="left:131px;top:74px"><div class="circ g"><span></span></div><div class="txt"><div class="t5">Title Goes Here</div><p class="p">Lorem ipsum dolor sit amet, consectetuer adipiscing elit, sed diam nonummy nibh euismod tincidunt ut laoreet dolore magna</p></div></div>
  <div class="item" style="left:10px;top:106px"><div class="circ g"><span></span></div><div class="txt"><div class="t5">Title Goes Here</div><p class="p">Lorem ipsum dolor sit amet, consectetuer adipiscing elit, sed diam nonummy nibh euismod tincidunt ut laoreet dolore magna</p></div></div>
  <div class="item" style="left:131px;top:106px"><div class="circ g"><span></span></div><div class="txt"><div class="t5">Title Goes Here</div><p class="p">Lorem ipsum dolor sit amet, consectetuer adipiscing elit, sed diam nonummy nibh euismod tincidunt ut laoreet dolore magna</p></div></div>
  <div class="foot"><span class="tick"></span><span class="mark"><i></i>NIVEL CREST</span><span class="bar"><span>www.nivelcrest.com</span><span>PAGE 01</span></span></div>
</section>

<!-- Team -->
<section class="slide" style="left:421px;top:516px">
  <div class="abs" style="left:0;right:0;top:19px;text-align:center;font-size:12px;font-weight:600;color:var(--ink)">OUR CREATIVE TEAM</div>
  <p class="p abs" style="left:36px;top:35px;width:188px;text-align:center">Lorem ipsum dolor sit amet, consectetuer adipiscing elit, sed diam nonummy nibh euismod tincidunt ut laoreet dolore magna aliquam erat volutpat. Ut wisi enim ad minim veniam, quis nostrud exerci tation ullamcorper suscipit lobortis nisl ut aliquip ex ea commodo consequat. Duis autem vel eum iriure dolor in hendre</p>
  <div class="abs" style="left:20px;top:58px;width:220px;display:flex;justify-content:space-between">
    <div style="width:50px;text-align:center"><div role="img" aria-label="Team member portrait" style="width:50px;height:50px;border-radius:50%;background:radial-gradient(circle at 40% 35%,var(--gold-lt),var(--gold))"></div><div class="t5" style="margin:6px 0 1px">Name Here</div><p class="p" style="text-align:center">Lorem ipsum dolor sit amet, consectetuer adipiscing elit, sed diam nonummy nibh euismod tincidunt ut laoreet dolore magna aliquam erat volutpat. Ut wisi enim ad minim veniam, quis</p></div>
    <div style="width:50px;text-align:center"><div role="img" aria-label="Team member portrait" style="width:50px;height:50px;border-radius:50%;background:radial-gradient(circle at 40% 35%,var(--gold-lt),var(--gold))"></div><div class="t5" style="margin:6px 0 1px">Name Here</div><p class="p" style="text-align:center">Lorem ipsum dolor sit amet, consectetuer adipiscing elit, sed diam nonummy nibh euismod tincidunt ut laoreet dolore magna aliquam erat volutpat. Ut wisi enim ad minim veniam, quis</p></div>
    <div style="width:50px;text-align:center"><div role="img" aria-label="Team member portrait" style="width:50px;height:50px;border-radius:50%;background:radial-gradient(circle at 40% 35%,var(--gold-lt),var(--gold))"></div><div class="t5" style="margin:6px 0 1px">Name Here</div><p class="p" style="text-align:center">Lorem ipsum dolor sit amet, consectetuer adipiscing elit, sed diam nonummy nibh euismod tincidunt ut laoreet dolore magna aliquam erat volutpat. Ut wisi enim ad minim veniam, quis</p></div>
    <div style="width:50px;text-align:center"><div role="img" aria-label="Team member portrait" style="width:50px;height:50px;border-radius:50%;background:radial-gradient(circle at 40% 35%,var(--gold-lt),var(--gold))"></div><div class="t5" style="margin:6px 0 1px">Name Here</div><p class="p" style="text-align:center">Lorem ipsum dolor sit amet, consectetuer adipiscing elit, sed diam nonummy nibh euismod tincidunt ut laoreet dolore magna aliquam erat volutpat. Ut wisi enim ad minim veniam, quis</p></div>
  </div>
  <div class="foot"><span class="tick"></span><span class="mark"><i></i>NIVEL CREST</span><span class="bar"><span>www.nivelcrest.com</span><span>PAGE 01</span></span></div>
</section>

<!-- Price table -->
<section class="slide" style="left:732px;top:516px">
  <div class="heading"><b>Heading</b> Goes Here</div>
  <div class="abs" style="left:84px;top:34px;width:42px;height:95px;border:1px solid var(--gold);border-radius:3px"></div>
  <table class="grid abs" style="left:10px;top:38px">
    <tr><th style="width:72px">Heading Goes Here</th><th style="background:var(--gold)">Heading<br>Goes Here</th><th>Heading<br>Goes Here</th><th>Heading<br>Goes Here</th><th>Heading<br>Goes Here</th></tr>
    <tr><td>Lorem Ipsum Goes Here</td><td>23</td><td>12</td><td>78</td><td>12</td></tr>
    <tr><td>Lorem Ipsum Goes Here</td><td>45</td><td>56</td><td>12</td><td>56</td></tr>
    <tr><td>Lorem Ipsum Goes Here</td><td>78</td><td>76</td><td>34</td><td>76</td></tr>
    <tr><td>Lorem Ipsum Goes Here</td><td>22</td><td>12</td><td>55</td><td>12</td></tr>
    <tr><td>Lorem Ipsum Goes Here</td><td>34</td><td>66</td><td>45</td><td>66</td></tr>
    <tr><td>Lorem Ipsum Goes Here</td><td>67</td><td>47</td><td>78</td><td>47</td></tr>
    <tr><td>Lorem Ipsum Goes Here</td><td>87</td><td>67</td><td>12</td><td>67</td></tr>
  </table>
  <div class="foot"><span class="tick"></span><span class="mark"><i></i>NIVEL CREST</span><span class="bar"><span>www.nivelcrest.com</span><span>PAGE 01</span></span></div>
</section>

<!-- Two column bullets -->
<section class="slide" style="left:111px;top:711px">
  <div class="heading"><b>Heading</b> Goes Here</div>
  <div class="abs" style="left:11px;top:34px;width:115px"><div class="sub" style="font-size:5.2px;color:var(--gold-dk);margin-bottom:6px">Curabitur Dapibus Dignissim Dui.</div>
    <ul class="bul p"><li>Lorem ipsum dolor sit amet, consectetuer adipiscing elit, sed diam nonummy nibh euismod tincidunt ut laoreet dolore magna aliquam erat volutpat. Ut wisi enim ad minim veniam,</li><li>Lorem ipsum dolor sit amet, consectetuer adipiscing elit, sed diam nonummy nibh euismod tincidunt ut laoreet dolore magna aliquam erat volutpat. Ut wisi enim ad minim veniam, quis nostrud exerci tation ullamcorper suscipit lobortis nisl ut aliquip ex ea commodo consequat. Duis autem vel eum iriure dolor in hendrerit in vulputate velit esse molestie consequat,</li><li>Lorem ipsum dolor sit amet, consectetuer adipiscing elit, sed diam nonummy nibh euismod tincidunt ut laoreet dolore magna aliquam erat volutpat. Ut wisi enim ad minim veniam, quis nostrud exerci tation ullamcorper suscipit lobortis nisl ut aliquip ex ea commodo consequat. Duis autem vel eum iriure dolor in hendrerit in vulputate velit esse molestie consequat,</li></ul></div>
  <div class="abs" style="left:135px;top:34px;width:115px"><div class="sub" style="font-size:5.2px;color:var(--gold-dk);margin-bottom:6px">Curabitur Dapibus Dignissim Dui.</div>
    <ul class="bul p"><li>Lorem ipsum dolor sit amet, consectetuer adipiscing elit, sed diam nonummy nibh euismod tincidunt ut laoreet dolore magna aliquam erat volutpat. Ut wisi enim ad minim veniam,</li><li>Lorem ipsum dolor sit amet, consectetuer adipiscing elit, sed diam nonummy nibh euismod tincidunt ut laoreet dolore magna aliquam erat volutpat. Ut wisi enim ad minim veniam, quis nostrud exerci tation ullamcorper suscipit lobortis nisl ut aliquip ex ea commodo consequat. Duis autem vel eum iriure dolor in hendrerit in vulputate velit esse molestie consequat,</li><li>Lorem ipsum dolor sit amet, consectetuer adipiscing elit, sed diam nonummy nibh euismod tincidunt ut laoreet dolore magna aliquam erat volutpat. Ut wisi enim ad minim veniam, quis nostrud exerci tation ullamcorper suscipit lobortis nisl ut aliquip ex ea commodo consequat. Duis autem vel eum iriure dolor in hendrerit in vulputate velit esse molestie consequat,</li></ul></div>
  <div class="foot"><span class="tick"></span><span class="mark"><i></i>NIVEL CREST</span><span class="bar"><span>www.nivelcrest.com</span><span>PAGE 01</span></span></div>
</section>

<!-- Arch cards -->
<section class="slide" style="left:421px;top:718px">
  <div class="heading"><b>Heading</b> Goes Here</div>
  <div class="abs" style="left:14px;top:46px;width:56px;height:86px;border-radius:10px 10px 0 0;background:linear-gradient(180deg,var(--gold-dk),var(--gold-lt) 60%,var(--gold));border-bottom:2px solid var(--dark)">
    <div style="width:7px;height:7px;border-radius:50%;background:var(--dark);margin:7px auto 0"></div>
    <div style="text-align:center;color:#fff;font-size:6px;margin:5px 0 3px">Heading</div>
    <p class="p" style="text-align:center;padding:0 8px">Lorem ipsum dolor sit amet, consectetuer adipiscing elit, sed diam nonummy nibh euismod tincidunt ut laoreet dolore magna aliquam erat volutpat. Ut wisi enim ad minim veniam, quis nostrud exerci tation</p></div>
  <div class="abs" style="left:76px;top:46px;width:56px;height:86px;border-radius:10px 10px 0 0;background:linear-gradient(180deg,var(--gold-dk),var(--gold-lt) 60%,var(--gold));border-bottom:2px solid var(--dark)">
    <div style="width:7px;height:7px;border-radius:50%;background:var(--dark);margin:7px auto 0"></div>
    <div style="text-align:center;color:#fff;font-size:6px;margin:5px 0 3px">Heading</div>
    <p class="p" style="text-align:center;padding:0 8px">Lorem ipsum dolor sit amet, consectetuer adipiscing elit, sed diam nonummy nibh euismod tincidunt ut laoreet dolore magna aliquam erat volutpat. Ut wisi enim ad minim veniam, quis nostrud exerci tation</p></div>
  <div class="abs" style="left:140px;top:46px;width:108px"><div class="sub" style="font-size:5.2px;color:var(--gold-dk);margin-bottom:6px">Curabitur Dapibus Dignissim Dui.</div>
    <ul class="bul p"><li>Lorem ipsum dolor sit amet, consectetuer adipiscing elit, sed diam nonummy nibh euismod tincidunt ut laoreet dolore magna aliquam erat volutpat. Ut wisi enim ad minim veniam,</li><li>Lorem ipsum dolor sit amet, consectetuer adipiscing elit, sed diam nonummy nibh euismod tincidunt ut laoreet dolore magna aliquam erat volutpat. Ut wisi enim ad minim veniam, quis nostrud exerci tation ullamcorper suscipit lobortis nisl ut aliquip ex ea commodo consequat. Duis autem vel eum iriure dolor in hendrerit in vulputate velit esse molestie consequat,</li><li>Lorem ipsum dolor sit amet, consectetuer adipiscing elit, sed diam nonummy nibh euismod tincidunt ut laoreet dolore magna aliquam erat volutpat. Ut wisi enim ad minim veniam, quis nostrud exerci tation ullamcorper suscipit lobortis nisl ut aliquip ex ea commodo consequat. Duis autem vel eum iriure dolor in hendrerit in vulputate velit esse molestie consequat,</li></ul></div>
  <div class="foot"><span class="tick"></span><span class="mark"><i></i>NIVEL CREST</span><span class="bar"><span>www.nivelcrest.com</span><span>PAGE 01</span></span></div>
</section>

<!-- Dark with icon grid -->
<section class="slide dark" style="left:732px;top:718px">
  <div class="heading">Heading Goes Here</div>
  <div class="abs" style="left:12px;top:53px;width:110px">
    <div class="t5" style="font-size:3.8px">Title Goes Here</div><p class="p" style="margin-bottom:4px">Lorem ipsum dolor sit amet, consectetuer adipiscing elit, sed diam nonummy nibh euismod tincidunt ut laoreet dolore magna aliquam erat volutpat. Ut wisi enim ad minim veniam, quis nostrud exerci tation ullamcorper suscipit lobortis nisl ut aliquip ex ea commodo consequat. Duis autem vel eum iriure dolor in hendre</p>
    <div class="t5" style="font-size:3.8px">Title Goes Here</div><p class="p" style="margin-bottom:4px">Lorem ipsum dolor sit amet, consectetuer adipiscing elit, sed diam nonummy nibh euismod tincidunt ut laoreet dolore magna aliquam erat volutpat. Ut wisi enim ad minim veniam, quis nostrud exerci tation ullamcorper suscipit lobortis nisl ut aliquip ex ea commodo consequat. Duis autem vel eum iriure dolor in hendre</p>
    <div class="t5" style="font-size:3.8px">Title Goes Here</div><p class="p">Lorem ipsum dolor sit amet, consectetuer adipiscing elit, sed diam nonummy nibh euismod tincidunt ut laoreet dolore magna aliquam erat volutpat. Ut wisi enim ad minim veniam, quis nostrud exerci tation ullamcorper suscipit lobortis nisl ut aliquip ex ea commodo consequat. Duis autem vel eum iriure dolor in hendre</p>
  </div>
  <div class="abs" style="left:146px;top:47px;width:104px;display:grid;grid-template-columns:1fr 1fr;column-gap:8px;row-gap:4px">
    <div style="text-align:center"><svg width="12" height="12" viewBox="0 0 12 12"><circle cx="6" cy="6" r="4" fill="none" stroke="var(--gold-lt)" stroke-width="1.6" stroke-dasharray="2 1"/></svg><p class="p">Lorem ipsum dolor sit amet, consectetuer adipiscing elit, sed diam nonummy nibh euismod tincidunt ut laoreet dolore magna aliquam erat vel eum iriure dolor in hendre</p></div>
    <div style="text-align:center"><svg width="12" height="12" viewBox="0 0 12 12"><circle cx="6" cy="6" r="4.5" fill="none" stroke="var(--gold-lt)"/><path d="M1.5 6h9M6 1.5v9" stroke="var(--gold-lt)" stroke-width=".7"/></svg><p class="p">Lorem ipsum dolor sit amet, consectetuer adipiscing elit, sed diam nonummy nibh euismod tincidunt ut laoreet dolore magna aliquam erat vel eum iriure dolor in hendre</p></div>
    <div style="text-align:center"><svg width="12" height="12" viewBox="0 0 12 12"><rect x="5" y="2" width="2" height="9" fill="var(--gold-lt)"/></svg><p class="p">Lorem ipsum dolor sit amet, consectetuer adipiscing elit, sed diam nonummy nibh euismod tincidunt ut laoreet dolore magna aliquam erat vel eum iriure dolor in hendre</p></div>
    <div style="text-align:center"><svg width="12" height="12" viewBox="0 0 12 12"><path d="M1 7 L5 4 L7 6 L11 3" stroke="var(--gold-lt)" fill="none" stroke-width="1.4"/></svg><p class="p">Lorem ipsum dolor sit amet, consectetuer adipiscing elit, sed diam nonummy nibh euismod tincidunt ut laoreet dolore magna aliquam erat vel eum iriure dolor in hendre</p></div>
  </div>
  <div class="foot"><span class="tick"></span><span class="mark"><i></i>NIVEL CREST</span><span class="bar"><span>www.nivelcrest.com</span><span>PAGE 01</span></span></div>
</section>

<!-- Gold with photos -->
<section class="slide gold" style="left:111px;top:919px">
  <div class="heading">Heading Goes Here</div>
  <div class="abs" style="left:10px;top:30px;width:242px">
    <p class="p">Northfield Metals Group is an exploration company with brownfield metals projects in North America. The company's strategy is to develop a portfolio of projects that support the green economy through the discovery and delivery of commodities that promote electrification and decarbonisation. We seek to maximise shareholder value through the acquisition, discovery, and advancement of high quality precious, base, and strategic metal projects in North America.</p><br>
    <p class="p">The company utilises the expertise of our North American exploration team to identify underexplored and undervalued high-grade metal projects with significant geological potential. The company has full ownership of the Ridge Valley Copper Project and the Stone Brook Gold Project. Both assets are located in the western United States.</p>
  </div>
  <div class="abs" style="left:12px;top:73px;width:238px;display:flex;justify-content:space-between">
    <div style="width:72px"><div role="img" aria-label="Office meeting around a table" style="height:36px;border:1.5px solid #fff;background:linear-gradient(135deg,#cfcfd2,#6d6e73)"></div><div style="text-align:center;font-size:4.3px;color:#fff;margin:4px 0 5px">Heading Goes Here</div><ul class="bul p" style="padding-left:4px"><li>Lorem ipsum dolor sit amet, consectetuer adipiscing edit. Vivamus eu dui ex.</li></ul></div>
    <div style="width:72px"><div role="img" aria-label="Person using a tablet with digital overlay" style="height:36px;border:1.5px solid #fff;background:linear-gradient(135deg,#a9c4dc,#3d5c7c)"></div><div style="text-align:center;font-size:4.3px;color:#fff;margin:4px 0 5px">Heading Goes Here</div><ul class="bul p" style="padding-left:4px"><li>Lorem ipsum dolor sit amet, consectetuer adipiscing edit. Vivamus eu dui ex.</li></ul></div>
    <div style="width:72px"><div role="img" aria-label="Consultants reviewing documents at a desk" style="height:36px;border:1.5px solid #fff;background:linear-gradient(135deg,#eef0f2,#9aa3ad)"></div><div style="text-align:center;font-size:4.3px;color:#fff;margin:4px 0 5px">Heading Goes Here</div><ul class="bul p" style="padding-left:4px"><li>Lorem ipsum dolor sit amet, consectetuer adipiscing edit. Vivamus eu dui ex.</li></ul></div>
  </div>
  <div class="foot"><span class="tick"></span><span class="mark"><i></i>NIVEL CREST</span><span class="bar"><span>www.nivelcrest.com</span><span>PAGE 01</span></span></div>
</section>

<!-- Infographic -->
<section class="slide" style="left:421px;top:919px">
  <div class="heading"><b>Heading</b> Goes Here</div>
  <div class="abs" style="left:0;right:0;top:29px;text-align:center;font-size:10.5px;font-weight:600;color:var(--gold)">INFOGRAPHIC CHART</div>
  <p class="p abs" style="left:40px;top:43px;width:180px;text-align:center">Lorem ipsum dolor sit amet, consectetuer adipiscing elit, sed diam nonummy nibh euismod tincidunt ut laoreet dolore magna aliquam erat volutpat. Ut wisi enim ad minim veniam, quis nostrud exerci tation ullamcorper suscipit lobortis nisl ut aliquip ex ea commodo consequat. Duis autem vel eum iriure dolor in hendre</p>
  <svg class="abs" style="left:94px;top:60px" width="72" height="72" viewBox="0 0 72 72">
    <circle cx="36" cy="36" r="35" fill="var(--gold)"/>
    <circle cx="36" cy="36" r="30" fill="none" stroke="var(--gold-lt)" stroke-width="2" opacity=".6"/>
    <circle cx="36" cy="36" r="22" fill="var(--dark)"/>
    <circle cx="36" cy="36" r="16" fill="#4a4a50"/>
    <g font-family="Montserrat,sans-serif" font-size="3.6" fill="#fff" text-anchor="middle" font-weight="600">
      <text x="36" y="7">50%</text><text x="36" y="68">50%</text>
      <text x="14" y="20">50%</text><text x="58" y="20">50%</text>
      <text x="9" y="38">50%</text><text x="63" y="38">50%</text>
      <text x="14" y="57">50%</text><text x="58" y="57">50%</text>
    </g>
  </svg>
  <div class="abs" style="left:38px;top:70px;width:50px;display:flex;flex-direction:column;gap:13px">
    <div style="display:flex;gap:3px"><i style="width:8px;height:6px;background:var(--gold);display:block;flex:none"></i><p class="p" style="font-size:1.9px">Lorem ipsum dolor sit amet, consectetuer adipiscing elit a. Praesent non nibh a libero egestas varius.</p></div>
    <div style="display:flex;gap:3px"><i style="width:7px;height:5px;border:.6px solid #555;display:block;flex:none"></i><p class="p" style="font-size:1.9px">Lorem ipsum dolor sit amet, consectetuer adipiscing elit a. Praesent non nibh a libero egestas varius.</p></div>
    <div style="display:flex;gap:3px"><i style="width:3px;height:7px;background:var(--gold);display:block;flex:none;margin:0 2px"></i><p class="p" style="font-size:1.9px">Lorem ipsum dolor sit amet, consectetuer adipiscing elit a. Praesent non nibh a libero egestas varius.</p></div>
  </div>
  <div class="abs" style="left:178px;top:70px;width:50px;display:flex;flex-direction:column;gap:13px">
    <div style="display:flex;gap:3px"><i style="width:6px;height:8px;border-radius:50% 50% 30% 30%;border:.8px solid var(--gold);display:block;flex:none"></i><p class="p" style="font-size:1.9px">Lorem ipsum dolor sit amet, consectetuer adipiscing elit a. Praesent non nibh a libero egestas varius.</p></div>
    <div style="display:flex;gap:3px"><i style="width:7px;height:7px;border-radius:50%;border:.8px solid var(--gold);display:block;flex:none"></i><p class="p" style="font-size:1.9px">Lorem ipsum dolor sit amet, consectetuer adipiscing elit a. Praesent non nibh a libero egestas varius.</p></div>
    <div style="display:flex;gap:3px"><i style="width:7px;height:7px;border-radius:50%;border:1.4px dotted var(--gold);display:block;flex:none"></i><p class="p" style="font-size:1.9px">Lorem ipsum dolor sit amet, consectetuer adipiscing elit a. Praesent non nibh a libero egestas varius.</p></div>
  </div>
  <div class="foot"><span class="tick"></span><span class="mark"><i></i>NIVEL CREST</span><span class="bar"><span>www.nivelcrest.com</span><span>PAGE 01</span></span></div>
</section>

<!-- Closing -->
<section class="slide" style="left:732px;top:919px">
  <div class="photo" role="img" aria-label="Golden-toned city skyline at sunset" style="background:linear-gradient(180deg,#8a7a55 0%,#c9a451 35%,#8f6d2c 70%,#3d2f18 100%)"></div>
  <div class="abs" style="left:0;right:0;top:15px;display:flex;justify-content:center;align-items:center;gap:3px;font-size:9px;font-weight:700;color:#fff"><i style="width:7px;height:7px;border:1px solid #fff;display:block"></i>NIVEL CREST</div>
  <div class="abs big" style="left:0;right:0;top:81px;font-size:34px;color:#fff">THANK YOU!</div>
  <div class="abs" style="left:0;right:0;top:123px;text-align:center;font-size:8px;font-weight:600;color:#fff">PRESENTATION</div>
  <div class="abs" style="left:0;right:0;top:132px;text-align:center;font-size:4.5px;font-weight:600;color:#fff">TITLE GOESHERE</div>
  <div class="abs" style="left:0;right:0;top:148px;text-align:center;font-size:3.6px;color:#fff">www.nivelcrest.com</div>
</section>

</main>
</body>
</html>
```